Tallow Reed Software

We are a software company selling endpoint visibility, access and security technology to enterprise-level IT departments.

Our technology helps organizations gain comprehensive visibility into and control over devices accessing their corporate network so they can quickly identify and address suspicious activity on the network that could lead to potential threats like data breaches.

This technology can cost organizations upwards of $1M - depending on the size of the organization. Our primary clients are Pinnacle 2,000 companies.

We want a professional, polished business card to represent our new brand.

Info fields to include on the card:
Name
Job Title
Office Phone #
Cell Phone #
Email address
Address: 4270 Vestridge Pond Blvd., Ste. 2600, Bloomington, MN 55812
Website address: www.tallowreedsoftware.example
Tagline: Discover the edge. Optimize the whole.

Logo files and color specs document are attached. Would like color scheme to coordinate with the logo.

Also looking at stationary/envelope designs in conjunction with the business card designs. Received very few designs that included the stationary.

Software

```html
<!DOCTYPE html>
<html lang="en">
<head>
<meta charset="utf-8">
<title>Tallow Reed Software — Business Card</title>
<link rel="stylesheet" href="https://fonts.googleapis.com/css2?family=PT+Sans:ital,wght@0,400;0,700;1,400&display=swap">
<style>
  :root {
    --backdrop: #e8e8e6;
    --card-dark: #3d393a;
    --card-red: #a72d33;
    --ink-light: #ffffff;
    --ink-soft: #f3dede;
  }
  html, body {
    margin: 0;
    padding: 0;
    width: 1200px;
    height: 1000px;
    overflow: hidden;
    background: var(--backdrop);
    font-family: "PT Sans", "Helvetica Neue", Arial, sans-serif;
  }
  .stage {
    position: relative;
    width: 1200px;
    height: 1000px;
  }
  .card {
    position: absolute;
    box-sizing: border-box;
    color: var(--ink-light);
  }
  .card--front {
    left: 230px;
    top: 392px;
    width: 333px;
    height: 216px;
    background: var(--card-dark);
    display: flex;
    align-items: center;
    justify-content: center;
  }
  .brand {
    display: flex;
    align-items: center;
    gap: 12px;
  }
  .brand__square {
    width: 14px;
    height: 14px;
    background: var(--ink-light);
  }
  .brand__name {
    font-weight: 700;
    font-size: 14px;
    line-height: 1.2;
    letter-spacing: 0.16em;
    text-transform: uppercase;
    color: var(--ink-light);
  }
  .card--back {
    left: 639px;
    top: 393px;
    width: 330px;
    height: 214px;
    background: var(--card-red);
  }
  .card__mark {
    position: absolute;
    right: 40px;
    top: 28px;
    width: 16px;
    height: 16px;
    background: var(--ink-light);
  }
  .person {
    position: absolute;
    left: 33px;
    top: 89px;
  }
  .person__name {
    margin: 0;
    font-size: 19px;
    font-weight: 400;
    line-height: 1.1;
  }
  .person__title {
    margin: 2px 0 0;
    font-size: 11.5px;
    font-style: italic;
    color: var(--ink-soft);
  }
  .contact {
    position: absolute;
    left: 33px;
    top: 158px;
    margin: 0;
    padding: 0;
    list-style: none;
    font-size: 8.6px;
    line-height: 12px;
    color: var(--ink-soft);
  }
</style>
</head>
<body>
  <main class="stage">
    <section class="card card--front" aria-label="Business card front">
      <div class="brand">
        <span class="brand__square" aria-hidden="true"></span>
        <span class="brand__name">Tallow Reed<br>Software</span>
      </div>
    </section>

    <section class="card card--back" aria-label="Business card back">
      <span class="card__mark" aria-hidden="true"></span>
      <div class="person">
        <h1 class="person__name">Evan Mercer</h1>
        <p class="person__title">Managing Director</p>
      </div>
      <ul class="contact">
        <li>Office: 555-1234-5678 / Cell : 555-1234-5678</li>
        <li>contact@tallowreedsoftware.example / www.tallowreedsoftware.example</li>
        <li>4270 Vestridge Pond Blvd., Ste. 2600, Bloomington, MN 55812</li>
      </ul>
    </section>
  </main>
</body>
</html>
```